Veriplume Digital Badge Header/Banner for Nimbleway People Certificaiton

We need a new page header/banner for Veriplume https://www.badgequill.example/ where we have all our digital badges and certificates for our Nimbleway People Coaching https://www.badgequill.example/issuer/48213/credentials

https://www.badgequill.example/group/503118
https://www.badgequill.example/group/514927
https://www.badgequill.example/group/520364

https://www.brightfernpartners.example/

Target Market(s)

HR Professionals

Font styles to use
Sans Serif

```html
<!DOCTYPE html>
<html lang="en">
<head>
<meta charset="utf-8">
<title>Veriplume – Nimbleway People Certificates Banner</title>
<link rel="stylesheet" href="https://fonts.googleapis.com/css2?family=Bebas+Neue&family=Oswald:wght@300;500&family=Montserrat:wght@400;500&display=swap">
<style>
  :root {
    --page-bg: #e9e9e9;
    --deep-blue: #1c3f9e;
    --violet: #4a2c9c;
    --purple: #5a3bb8;
    --cyan: #22d6e6;
    --white: #ffffff;
    --ink: #1f2a30;
    --swoosh: #0f2f39;
    --ribbon: #5f909f;
    --ribbon-dark: #3b6877;
    --pattern: #e6e3d0;
    --rule: #b9b9b9;
    --badge-trainer: #d92434;
    --badge-coach: #ee7d1f;
    --badge-professional: #1fa6a3;
    --badge-practitioner: #8bc43f;
    --badge-explorer: #7a3590;
  }
  * { margin: 0; padding: 0; box-sizing: border-box; }
  html, body { width: 1200px; height: 447px; overflow: hidden; background: var(--page-bg); }
  .canvas { position: relative; width: 1200px; height: 447px; }

  .banner {
    position: absolute; left: 49px; top: 139px; width: 1102px; height: 170px;
    overflow: hidden;
    background:
      radial-gradient(ellipse 260px 110px at 1080px 170px, rgba(34,214,230,.95), rgba(34,214,230,0) 70%),
      radial-gradient(ellipse 200px 90px at 30px 20px, rgba(40,110,220,.7), rgba(40,110,220,0) 70%),
      radial-gradient(ellipse 380px 120px at 700px 160px, rgba(120,80,220,.55), rgba(120,80,220,0) 70%),
      linear-gradient(90deg, var(--deep-blue) 0%, #2a2f8e 25%, var(--violet) 50%, var(--purple) 75%, #3f6fd6 100%);
  }

  .headline { position: absolute; left: 20px; top: 34px; width: 280px; color: var(--white); }
  .headline-title {
    font-family: "Bebas Neue", sans-serif; font-size: 60px; line-height: 1;
    letter-spacing: 0; text-shadow: 2px 3px 6px rgba(0,0,0,.25);
  }
  .headline-sub {
    margin-top: 14px; font-family: "Oswald", sans-serif; font-size: 19px;
    line-height: 1; text-transform: uppercase; white-space: nowrap; letter-spacing: -.2px;
  }
  .headline-sub .light { font-weight: 300; }
  .headline-sub .bold { font-weight: 500; }

  .certificate {
    position: absolute; top: 27px; width: 140px; height: 108px;
    background: var(--white); box-shadow: 0 6px 14px rgba(10,10,60,.35);
  }
  .certificate svg { display: block; width: 140px; height: 108px; }
  .cert-heading { font-family: "Montserrat", sans-serif; fill: var(--ink); }
  .cert-brand { font-family: "Montserrat", sans-serif; font-weight: 500; fill: var(--white); }
  .cert-ribbon-text { font-family: "Montserrat", sans-serif; font-weight: 500; fill: var(--white); letter-spacing: .6px; }
  .cert-small { font-family: "Montserrat", sans-serif; fill: #555; }
</style>
</head>
<body>
<div class="canvas">
  <section class="banner">
    <div class="headline">
      <h1 class="headline-title">CERTIFICATES</h1>
      <p class="headline-sub"><span class="light">For our </span><span class="bold">Nimbleway People Coaching</span></p>
    </div>

    <!-- certificate template repeated per level -->
    <article class="certificate" style="left:323px">
      <svg viewBox="0 0 300 232" aria-label="Nimbleway People Trainer certificate">
        <path d="M40,52 C120,34 190,8 250,0 L300,0 L300,4 C230,12 150,34 40,56 Z" fill="#d6d9db"/>
        <path d="M0,58 C90,50 160,22 230,12 C262,7 286,3 300,2 L300,42 C220,44 120,56 0,62 Z" fill="var(--swoosh)"/>
        <text class="cert-heading" x="25" y="30" font-size="19">CERTIFICATE</text>
        <text class="cert-heading" x="25" y="40" font-size="8.5">OF COMPLETION</text>
        <text class="cert-brand" x="265" y="31" font-size="10" text-anchor="middle">BRIGHTFERN</text>
        <rect role="img" aria-label="Decorative dotted pattern" x="12" y="74" width="85" height="140" rx="40" fill="var(--pattern)" opacity=".8"/>
        <path d="M22,86 L48,86 L44,94 L48,102 L22,102 L30,94 Z" fill="var(--ribbon-dark)"/>
        <path d="M278,86 L252,86 L256,94 L252,102 L278,102 L270,94 Z" fill="var(--ribbon-dark)"/>
        <rect x="42" y="81" width="216" height="21" fill="var(--ribbon)"/>
        <text class="cert-ribbon-text" x="150" y="95" font-size="9.5" text-anchor="middle">NIMBLEWAY PEOPLE TRAINER</text>
        <text class="cert-small" x="150" y="118" font-size="5.5" text-anchor="middle">This certificate is proudly presented to</text>
        <line x1="60" y1="142" x2="270" y2="142" stroke="var(--rule)" stroke-width=".8"/>
        <text class="cert-small" x="150" y="151" font-size="4" text-anchor="middle">for completing the certification course and</text>
        <text class="cert-small" x="150" y="156" font-size="4" text-anchor="middle">meeting all requirements</text>
        <line x1="72" y1="193" x2="125" y2="193" stroke="var(--rule)" stroke-width=".8"/>
        <text class="cert-small" x="98" y="200" font-size="4.5" text-anchor="middle">New York City</text>
        <circle cx="150" cy="188" r="19" fill="var(--badge-trainer)"/>
        <circle cx="150" cy="188" r="14" fill="#2a2530"/>
        <line x1="185" y1="193" x2="245" y2="193" stroke="var(--rule)" stroke-width=".8"/>
        <text class="cert-small" x="215" y="200" font-size="4.5" text-anchor="middle">Marisol Trenholm</text>
      </svg>
    </article>

    <article class="certificate" style="left:479px">
      <svg viewBox="0 0 300 232" aria-label="Nimbleway People Coach certificate">
        <path d="M40,52 C120,34 190,8 250,0 L300,0 L300,4 C230,12 150,34 40,56 Z" fill="#d6d9db"/>
        <path d="M0,58 C90,50 160,22 230,12 C262,7 286,3 300,2 L300,42 C220,44 120,56 0,62 Z" fill="var(--swoosh)"/>
        <text class="cert-heading" x="25" y="30" font-size="19">CERTIFICATE</text>
        <text class="cert-heading" x="25" y="40" font-size="8.5">OF COMPLETION</text>
        <text class="cert-brand" x="265" y="31" font-size="10" text-anchor="middle">BRIGHTFERN</text>
        <rect role="img" aria-label="Decorative dotted pattern" x="12" y="74" width="85" height="140" rx="40" fill="var(--pattern)" opacity=".8"/>
        <path d="M22,86 L48,86 L44,94 L48,102 L22,102 L30,94 Z" fill="var(--ribbon-dark)"/>
        <path d="M278,86 L252,86 L256,94 L252,102 L278,102 L270,94 Z" fill="var(--ribbon-dark)"/>
        <rect x="42" y="81" width="216" height="21" fill="var(--ribbon)"/>
        <text class="cert-ribbon-text" x="150" y="95" font-size="9.5" text-anchor="middle">NIMBLEWAY PEOPLE COACH</text>
        <text class="cert-small" x="150" y="118" font-size="5.5" text-anchor="middle">This certificate is proudly presented to</text>
        <line x1="60" y1="142" x2="270" y2="142" stroke="var(--rule)" stroke-width=".8"/>
        <text class="cert-small" x="150" y="151" font-size="4" text-anchor="middle">for completing the certification course and</text>
        <text class="cert-small" x="150" y="156" font-size="4" text-anchor="middle">meeting all requirements</text>
        <line x1="72" y1="193" x2="125" y2="193" stroke="var(--rule)" stroke-width=".8"/>
        <text class="cert-small" x="98" y="200" font-size="4.5" text-anchor="middle">New York City</text>
        <circle cx="150" cy="188" r="19" fill="var(--badge-coach)"/>
        <circle cx="150" cy="188" r="14" fill="#2a2530"/>
        <line x1="185" y1="193" x2="245" y2="193" stroke="var(--rule)" stroke-width=".8"/>
        <text class="cert-small" x="215" y="200" font-size="4.5" text-anchor="middle">Marisol Trenholm</text>
      </svg>
    </article>

    <article class="certificate" style="left:634px">
      <svg viewBox="0 0 300 232" aria-label="Nimbleway People Professional certificate">
        <path d="M40,52 C120,34 190,8 250,0 L300,0 L300,4 C230,12 150,34 40,56 Z" fill="#d6d9db"/>
        <path d="M0,58 C90,50 160,22 230,12 C262,7 286,3 300,2 L300,42 C220,44 120,56 0,62 Z" fill="var(--swoosh)"/>
        <text class="cert-heading" x="25" y="30" font-size="19">CERTIFICATE</text>
        <text class="cert-heading" x="25" y="40" font-size="8.5">OF COMPLETION</text>
        <text class="cert-brand" x="265" y="31" font-size="10" text-anchor="middle">BRIGHTFERN</text>
        <rect role="img" aria-label="Decorative dotted pattern" x="12" y="74" width="85" height="140" rx="40" fill="var(--pattern)" opacity=".8"/>
        <path d="M22,86 L48,86 L44,94 L48,102 L22,102 L30,94 Z" fill="var(--ribbon-dark)"/>
        <path d="M278,86 L252,86 L256,94 L252,102 L278,102 L270,94 Z" fill="var(--ribbon-dark)"/>
        <rect x="42" y="81" width="216" height="21" fill="var(--ribbon)"/>
        <text class="cert-ribbon-text" x="150" y="95" font-size="9.5" text-anchor="middle">NIMBLEWAY PEOPLE PROFESSIONAL</text>
        <text class="cert-small" x="150" y="118" font-size="5.5" text-anchor="middle">This certificate is proudly presented to</text>
        <line x1="60" y1="142" x2="270" y2="142" stroke="var(--rule)" stroke-width=".8"/>
        <text class="cert-small" x="150" y="151" font-size="4" text-anchor="middle">for completing the certification course and</text>
        <text class="cert-small" x="150" y="156" font-size="4" text-anchor="middle">meeting all requirements</text>
        <line x1="72" y1="193" x2="125" y2="193" stroke="var(--rule)" stroke-width=".8"/>
        <text class="cert-small" x="98" y="200" font-size="4.5" text-anchor="middle">New York City</text>
        <circle cx="150" cy="188" r="19" fill="var(--badge-professional)"/>
        <circle cx="150" cy="188" r="14" fill="#2a2530"/>
        <line x1="185" y1="193" x2="245" y2="193" stroke="var(--rule)" stroke-width=".8"/>
        <text class="cert-small" x="215" y="200" font-size="4.5" text-anchor="middle">Marisol Trenholm</text>
      </svg>
    </article>

    <article class="certificate" style="left:790px">
      <svg viewBox="0 0 300 232" aria-label="Nimbleway People Practitioner certificate">
        <path d="M40,52 C120,34 190,8 250,0 L300,0 L300,4 C230,12 150,34 40,56 Z" fill="#d6d9db"/>
        <path d="M0,58 C90,50 160,22 230,12 C262,7 286,3 300,2 L300,42 C220,44 120,56 0,62 Z" fill="var(--swoosh)"/>
        <text class="cert-heading" x="25" y="30" font-size="19">CERTIFICATE</text>
        <text class="cert-heading" x="25" y="40" font-size="8.5">OF COMPLETION</text>
        <text class="cert-brand" x="265" y="31" font-size="10" text-anchor="middle">BRIGHTFERN</text>
        <rect role="img" aria-label="Decorative dotted pattern" x="12" y="74" width="85" height="140" rx="40" fill="var(--pattern)" opacity=".8"/>
        <path d="M22,86 L48,86 L44,94 L48,102 L22,102 L30,94 Z" fill="var(--ribbon-dark)"/>
        <path d="M278,86 L252,86 L256,94 L252,102 L278,102 L270,94 Z" fill="var(--ribbon-dark)"/>
        <rect x="42" y="81" width="216" height="21" fill="var(--ribbon)"/>
        <text class="cert-ribbon-text" x="150" y="95" font-size="9.5" text-anchor="middle">NIMBLEWAY PEOPLE PRACTITIONER</text>
        <text class="cert-small" x="150" y="118" font-size="5.5" text-anchor="middle">This certificate is proudly presented to</text>
        <line x1="60" y1="142" x2="270" y2="142" stroke="var(--rule)" stroke-width=".8"/>
        <text class="cert-small" x="150" y="151" font-size="4" text-anchor="middle">for completing the certification course and</text>
        <text class="cert-small" x="150" y="156" font-size="4" text-anchor="middle">meeting all requirements</text>
        <line x1="72" y1="193" x2="125" y2="193" stroke="var(--rule)" stroke-width=".8"/>
        <text class="cert-small" x="98" y="200" font-size="4.5" text-anchor="middle">New York City</text>
        <circle cx="150" cy="188" r="19" fill="var(--badge-practitioner)"/>
        <circle cx="150" cy="188" r="14" fill="#2a2530"/>
        <line x1="185" y1="193" x2="245" y2="193" stroke="var(--rule)" stroke-width=".8"/>
        <text class="cert-small" x="215" y="200" font-size="4.5" text-anchor="middle">Marisol Trenholm</text>
      </svg>
    </article>

    <article class="certificate" style="left:945px">
      <svg viewBox="0 0 300 232" aria-label="Nimbleway People Explorer certificate">
        <path d="M40,52 C120,34 190,8 250,0 L300,0 L300,4 C230,12 150,34 40,56 Z" fill="#d6d9db"/>
        <path d="M0,58 C90,50 160,22 230,12 C262,7 286,3 300,2 L300,42 C220,44 120,56 0,62 Z" fill="var(--swoosh)"/>
        <text class="cert-heading" x="25" y="30" font-size="19">CERTIFICATE</text>
        <text class="cert-heading" x="25" y="40" font-size="8.5">OF COMPLETION</text>
        <text class="cert-brand" x="265" y="31" font-size="10" text-anchor="middle">BRIGHTFERN</text>
        <rect role="img" aria-label="Decorative dotted pattern" x="12" y="74" width="85" height="140" rx="40" fill="var(--pattern)" opacity=".8"/>
        <path d="M22,86 L48,86 L44,94 L48,102 L22,102 L30,94 Z" fill="var(--ribbon-dark)"/>
        <path d="M278,86 L252,86 L256,94 L252,102 L278,102 L270,94 Z" fill="var(--ribbon-dark)"/>
        <rect x="42" y="81" width="216" height="21" fill="var(--ribbon)"/>
        <text class="cert-ribbon-text" x="150" y="95" font-size="9.5" text-anchor="middle">NIMBLEWAY PEOPLE EXPLORER</text>
        <text class="cert-small" x="150" y="118" font-size="5.5" text-anchor="middle">This certificate is proudly presented to</text>
        <line x1="60" y1="142" x2="270" y2="142" stroke="var(--rule)" stroke-width=".8"/>
        <text class="cert-small" x="150" y="151" font-size="4" text-anchor="middle">for completing the certification course and</text>
        <text class="cert-small" x="150" y="156" font-size="4" text-anchor="middle">meeting all requirements</text>
        <line x1="72" y1="193" x2="125" y2="193" stroke="var(--rule)" stroke-width=".8"/>
        <text class="cert-small" x="98" y="200" font-size="4.5" text-anchor="middle">New York City</text>
        <circle cx="150" cy="188" r="19" fill="var(--badge-explorer)"/>
        <circle cx="150" cy="188" r="14" fill="#2a2530"/>
        <line x1="185" y1="193" x2="245" y2="193" stroke="var(--rule)" stroke-width=".8"/>
        <text class="cert-small" x="215" y="200" font-size="4.5" text-anchor="middle">Marisol Trenholm</text>
      </svg>
    </article>
  </section>
</div>
</body>
</html>
```